Professional, Attractive, Simple Website Needed!!

We completed the design for our logo.

We need a website built out around this.

Here are a couple samples of how we want ours formatted.

http://brimvoltco.com

http://www.ravelbeam.com/lp/free-quote?LeadSource=Search%20Engine&ProgramName=searchads&experience=qual&language=en&type=brd&gclid=Xk7PLmqwTRZBNVuEYcaHdFgWsLoPeRtQnMxVbCzJaKiOuYtReWqAsDfGhJkLzXcVbNmQwErTyUiOpAsDfGhJkLzX_wcB

http://quorel.co
Updates

Project Deadline Extended
Reason: Extending this deadline due to our delay in providing designers with content for each page. This is coming in next 24 hours.

Project Deadline Extended
Reason: Due to scheduling conflicts and extended travel delays related to Puerto Rico, the deadline has been extended. Your patience is greatly appreciated.

Project Deadline Extended
Reason: Travel and scheduling conflicts have made it impossible to give this project the thorough review it deserves, therefore I am extending the deadline. Thank you for your patience!

Target Market(s)

Home Owners who earn 60k + household annually

Industry/Entity Type

It Professional

Coding

Coded - Design and coding required

Number of Pages Required

5+ page

Font styles to use
Serif

Colors
34a7d8
9bcb3c

Requirements
Must have
• Simple
• Lead form Entry (Ability for visitor to enter Name, number and address for a quote)
• Sleek Design
• Professional
• Testimonials
• Use color Scheme of Design Logo Attached
Nice to have
• Video when site starts
• Like this
• https://www.vidplexa.com/watch?v=Qm8rTbLw3Np&feature=vidplexa.be
Should not have
• Should not include Commercial solar
• Should not include wind power

```html
<!DOCTYPE html>
<html lang="en">
<head>
<meta charset="utf-8">
<title>Halvora Energy – Home Solar</title>
<link href="https://fonts.googleapis.com/css2?family=Open+Sans:wght@400;600;700;800&display=swap" rel="stylesheet">
<style>
  :root {
    --blue: #34a7d8;
    --green: #9bcb3c;
    --ink: #2b2f33;
    --muted: #8a9097;
    --rule: #e3e6e9;
    --white: #ffffff;
    --hero-sky: #6f9fc4;
    --hero-roof: #7b5a44;
    --field-sky: #8fc6ea;
    --field-grass: #6f9a3c;
  }
  * { box-sizing: border-box; margin: 0; padding: 0; }
  html, body { width: 851px; height: 1200px; overflow: hidden; background: var(--white); }
  body { font-family: "Open Sans", Arial, sans-serif; color: var(--ink); position: relative; }

  /* Navigation */
  .site-nav { position: absolute; top: 0; left: 0; width: 851px; height: 56px; background: var(--white); z-index: 5; }
  .nav-group { position: absolute; top: 0; height: 56px; display: flex; align-items: center; gap: 30px; list-style: none; }
  .nav-group.left { left: 112px; }
  .nav-group.right { right: 112px; }
  .nav-group a { font-size: 8px; font-weight: 700; letter-spacing: .6px; color: var(--ink); text-decoration: none; text-transform: uppercase; }
  .nav-group a.active { color: var(--green); }

  .brand { position: absolute; left: 50%; transform: translateX(-50%); border-radius: 50%; background: var(--white);
           border: 3px solid var(--blue); box-shadow: 0 0 0 3px var(--green); display: flex; align-items: center; justify-content: center; }
  .brand span { font-weight: 800; color: var(--blue); letter-spacing: .5px; text-align: center; line-height: 1.15; }
  .brand.header { top: 8px; width: 96px; height: 96px; z-index: 6; }
  .brand.header span { font-size: 13px; }
  .brand.footer { top: 1036px; width: 66px; height: 66px; }
  .brand.footer span { font-size: 9px; }

  /* Hero */
  .hero { position: absolute; top: 56px; left: 0; width: 851px; height: 370px;
          background: linear-gradient(180deg, var(--hero-sky) 0%, #9cb7c9 40%, var(--hero-roof) 72%, #5d6b3a 100%); }
  .play-button { position: absolute; top: 98px; left: 403px; width: 44px; height: 44px; border-radius: 50%;
                 background: var(--white); box-shadow: 0 0 0 4px rgba(255,255,255,.5); display: flex; align-items: center; justify-content: center; z-index: 2; }
  .quote-card { position: absolute; top: 120px; left: 372px; width: 186px; height: 196px; border-radius: 8px;
                background: linear-gradient(160deg, rgba(52,167,216,.92) 0%, rgba(155,203,60,.92) 100%); padding: 30px 13px 0; text-align: center; }
  .quote-card h2 { color: var(--white); font-size: 13px; font-weight: 700; margin-bottom: 10px; }
  .quote-field { display: block; width: 160px; height: 18px; border: 1px solid rgba(255,255,255,.85); border-radius: 10px;
                 margin-bottom: 8px; padding-left: 10px; font-size: 6px; line-height: 16px; color: var(--white); text-align: left; }
  .quote-submit { display: inline-block; margin-top: 6px; padding: 0 14px; height: 18px; line-height: 16px; border: 1px solid var(--white);
                  border-radius: 10px; font-size: 6px; font-weight: 700; color: var(--white); letter-spacing: .5px; }
  .scroll-down { position: absolute; top: 338px; left: 416px; width: 18px; height: 18px; border-radius: 50%; border: 1px solid var(--white);
                 display: flex; align-items: center; justify-content: center; }

  /* Benefits */
  .benefits { position: absolute; top: 480px; left: 0; width: 851px; display: flex; justify-content: center; gap: 52px; }
  .benefit { width: 148px; text-align: center; }
  .benefit-icon { width: 52px; height: 52px; margin: 0 auto 10px; border-radius: 50%; padding: 3px;
                  background: linear-gradient(135deg, var(--blue), var(--green)); }
  .benefit-icon div { width: 100%; height: 100%; border-radius: 50%; background: var(--white); display: flex; align-items: center; justify-content: center; }
  .benefit h3 { font-size: 12px; font-weight: 700; margin-bottom: 7px; }
  .benefit p { font-size: 6.5px; line-height: 1.55; color: var(--muted); }

  /* Testimonials */
  .testimonial-scene { position: absolute; top: 708px; left: 0; width: 851px; height: 312px;
                       background: linear-gradient(180deg, #4d9bd6 0%, var(--field-sky) 55%, #b8d6a0 78%, var(--field-grass) 100%); }
  .testimonial-card { position: absolute; top: 762px; left: 115px; width: 430px; height: 232px; border-radius: 8px;
                      background: linear-gradient(150deg, rgba(52,167,216,.8) 0%, rgba(120,190,80,.82) 100%); padding: 22px 24px; color: var(--white); }
  .testimonial-card h2 { font-size: 20px; font-weight: 600; }
  .slider-controls { position: absolute; top: 24px; right: 24px; display: flex; gap: 6px; }
  .slider-controls span { width: 16px; height: 16px; border-radius: 50%; background: rgba(255,255,255,.9); display: flex; align-items: center; justify-content: center; }
  .reviewer { margin-top: 16px; height: 48px; display: flex; align-items: center; gap: 10px; }
  .reviewer-photo { width: 36px; height: 36px; border-radius: 50%; background: #d7dde2; border: 2px solid var(--white); }
  .reviewer-name { font-size: 10px; font-weight: 700; }
  .reviewer-role { font-size: 6.5px; opacity: .9; }
  .review-date { margin-left: auto; font-size: 7px; }
  .review-rule { height: 1px; background: rgba(255,255,255,.6); margin: 10px 0 14px; }
  .review-body { display: flex; gap: 10px; }
  .review-body p { font-size: 7.5px; line-height: 1.6; }

  /* Footer */
  .footer-links { position: absolute; top: 1064px; left: 70px; font-size: 6.5px; font-weight: 700; letter-spacing: .4px; text-transform: uppercase; }
  .footer-links a { color: var(--ink); text-decoration: none; }
  .footer-legal { position: absolute; top: 1064px; right: 70px; font-size: 6.5px; font-weight: 700; letter-spacing: .4px; text-transform: uppercase; }
  .footer-rule { position: absolute; top: 1116px; left: 70px; width: 711px; height: 1px; background: var(--rule); }
  .disclaimer { position: absolute; top: 1126px; left: 130px; width: 591px; text-align: center; color: var(--muted); }
  .disclaimer h4 { font-size: 6px; font-weight: 700; letter-spacing: .5px; color: var(--ink); margin-bottom: 5px; }
  .disclaimer p { font-size: 5.5px; line-height: 1.6; }
</style>
</head>
<body>

<nav class="site-nav">
  <ul class="nav-group left">
    <li><a class="active" href="#">Home</a></li>
    <li><a href="#">About Us</a></li>
    <li><a href="#">How It Works</a></li>
  </ul>
  <ul class="nav-group right">
    <li><a href="#">FAQ's</a></li>
    <li><a href="#">Testimonials</a></li>
    <li><a href="#">Contact Us</a></li>
  </ul>
</nav>
<div class="brand header"><span>HALVORA<br>ENERGY</span></div>

<header class="hero" role="img" aria-label="Photo of a house roof fitted with solar panels under a blue sky">
  <div class="play-button">
    <svg width="14" height="16" viewBox="0 0 14 16"><path d="M2 1 L13 8 L2 15 Z" fill="#2b2f33"/></svg>
  </div>
  <form class="quote-card">
    <h2>Get Free Quote</h2>
    <span class="quote-field">Name</span>
    <span class="quote-field">Phone Number</span>
    <span class="quote-field">Address</span>
    <span class="quote-submit">GET A QUOTE</span>
  </form>
  <div class="scroll-down">
    <svg width="8" height="6" viewBox="0 0 8 6"><path d="M1 1 L4 4.5 L7 1" fill="none" stroke="#fff" stroke-width="1.3"/></svg>
  </div>
</header>

<section class="benefits">
  <article class="benefit">
    <div class="benefit-icon"><div>
      <svg width="22" height="24" viewBox="0 0 22 24" fill="none" stroke="#2b2f33" stroke-width="1.6">
        <path d="M11 2 a7 7 0 0 1 4 12.7 V17 H7 V14.7 A7 7 0 0 1 11 2 Z"/><path d="M8 20 H14 M9 23 H13"/>
      </svg>
    </div></div>
    <h3>Free Cost</h3>
    <p>Lorem ipsum dolor sit amet, consectetur adipiscing elit, sed do eiusmod tempor incididunt ut labore et.</p>
  </article>
  <article class="benefit">
    <div class="benefit-icon"><div>
      <svg width="22" height="24" viewBox="0 0 22 24" fill="none" stroke="#2b2f33" stroke-width="1.6">
        <path d="M11 2 a7 7 0 0 1 4 12.7 V17 H7 V14.7 A7 7 0 0 1 11 2 Z"/><path d="M8 20 H14 M9 23 H13"/>
        <path d="M13 6.5 H10 a1.5 1.5 0 0 0 0 3 H12 a1.5 1.5 0 0 1 0 3 H9 M11 5 V14" stroke-width="1.1"/>
      </svg>
    </div></div>
    <h3>Low Energy Bills</h3>
    <p>Lorem ipsum dolor sit amet, consectetur adipiscing elit, sed do eiusmod tempor incididunt ut labore et.</p>
  </article>
  <article class="benefit">
    <div class="benefit-icon"><div>
      <svg width="24" height="24" viewBox="0 0 24 24" fill="none" stroke="#2b2f33" stroke-width="1.8" stroke-linecap="round">
        <path d="M4 20 L14 10 M14 10 a4 4 0 1 0 4 -6 L15 7 L17 9 L20 6 a4 4 0 0 1 -6 4"/>
        <path d="M5 4 L20 19 M3 6 L7 2"/>
      </svg>
    </div></div>
    <h3>Maintenance Free</h3>
    <p>Lorem ipsum dolor sit amet, consectetur adipiscing elit, sed do eiusmod tempor incididunt ut labore et.</p>
  </article>
</section>

<section class="testimonial-scene" role="img" aria-label="Photo of a happy family outdoors on a sunny day with blue sky and green field"></section>
<div class="testimonial-card">
  <h2>Testimonials</h2>
  <div class="slider-controls">
    <span><svg width="6" height="8" viewBox="0 0 6 8"><path d="M5 1 L1.5 4 L5 7" fill="none" stroke="#3a8fb5" stroke-width="1.4"/></svg></span>
    <span><svg width="6" height="8" viewBox="0 0 6 8"><path d="M1 1 L4.5 4 L1 7" fill="none" stroke="#3a8fb5" stroke-width="1.4"/></svg></span>
  </div>
  <div class="reviewer">
    <div class="reviewer-photo" role="img" aria-label="Reviewer portrait"></div>
    <div>
      <div class="reviewer-name">Daniel Morrow</div>
      <div class="reviewer-role">Energy Instructor</div>
    </div>
    <div class="review-date">1 Day ago</div>
  </div>
  <div class="review-rule"></div>
  <div class="review-body">
    <svg width="16" height="12" viewBox="0 0 16 12" fill="#fff"><path d="M0 12 V6 Q0 1 6 0 V2 Q3 3 3 6 H6 V12 Z M9 12 V6 Q9 1 15 0 V2 Q12 3 12 6 H15 V12 Z"/></svg>
    <p>Switching our home to solar was simple from the first call to the final install. The team explained every step, the panels look great, and our monthly energy bills have dropped more than we expected.</p>
  </div>
</div>

<footer>
  <div class="footer-links"><a href="#">Terms of Use</a> &nbsp;|&nbsp; <a href="#">Careers</a> &nbsp;|&nbsp; <a href="#">Privacy Policy</a></div>
  <div class="brand footer"><span>HALVORA<br>ENERGY</span></div>
  <div class="footer-legal">© 2017 Company Name &nbsp;|&nbsp; All Rights Reserved</div>
  <div class="footer-rule"></div>
  <div class="disclaimer">
    <h4>DISCLAIMER</h4>
    <p>Savings shown are estimates only and depend on your home, roof orientation, local utility rates, incentives and energy use. Actual results may vary. Quotes are provided free and without obligation, and all installations are subject to a site survey and approval.</p>
  </div>
</footer>

</body>
</html>
```